Business Cards Needed for Innovative Healthcare Marketing Company

We are a marketing company focused on healthcare. Our company is all about rebranding yourself renewing your image and generating results. The phoenix stands for "reborn" or "rising" which we provide new brands for our clients we take their old brands and renew it with creativity and innovation. I am looking for a business card with color dimension. I have attached an example of a card I think has the look and feel of what I am trying to accomplish. I like that the card example has black and grey font colors, I like the font placement and the small logo, I really like the use of the colors on the right those are the colors of my logo. My logo is phoenix so maybe incorporating flames similar to that design. I would like the back a solid color maybe red with an opaque version of the logo and website. As a marketing company I am always open to creative liberty!

Target Market(s)

Doctors and business professionals.

Industry/Entity Type

Marketing

Contact Information for Business Card

Valcorne Health Care Marketing
Marla Tenwick- CEO
#(512)638-2974
email-marla@valcorne.com
website- valcorne.com

Font styles to use
Sans Serif

Colors
ec1f27
f37122
ffc214
fbed22
fbf289
f04a50

Requirements
Must have
• The logo and required information
Nice to have
• icons by the information
Should not have
• child like font

```html
<!DOCTYPE html>
<html lang="en">
<head>
<meta charset="utf-8">
<title>Valcorne Health Care Marketing – Business Card</title>
<link rel="stylesheet" href="https://fonts.googleapis.com/css2?family=Open+Sans:wght@400;600;700&display=swap">
<style>
  :root {
    --stage: #2b2b2b;
    --card-white: #ffffff;
    --card-black: #000000;
    --brand-red: #9b1c22;
    --flame-orange: #d6621f;
    --accent-gold: #f2a22b;
    --text-white: #ffffff;
  }
  * { box-sizing: border-box; margin: 0; padding: 0; }
  html, body { width: 1200px; height: 987px; overflow: hidden; }
  body {
    background: var(--stage);
    font-family: "Open Sans", Arial, sans-serif;
    position: relative;
  }
  .card {
    position: absolute;
    left: 293px;
    width: 614px;
    height: 352px;
    overflow: hidden;
  }
  .card-front { top: 125px; background: var(--card-white); }
  .card-back { top: 511px; background: var(--card-black); }

  .swoosh { position: absolute; inset: 0; width: 100%; height: 100%; }

  .brand-mark {
    position: absolute;
    border-radius: 50%;
    background: var(--flame-orange);
  }
  .front-mark { left: 52px; top: 46px; width: 96px; height: 96px; }
  .back-mark { left: 257px; top: 92px; width: 100px; height: 100px; }

  .wordmark {
    position: absolute;
    color: var(--brand-red);
    font-weight: 400;
    line-height: 1;
  }
  .wordmark .name { display: block; font-size: 40px; letter-spacing: 1px; }
  .wordmark .tagline { display: block; font-size: 13px; letter-spacing: 0.8px; margin-top: 8px; }
  .front-wordmark { left: 172px; top: 98px; }
  .back-wordmark { left: 0; right: 0; top: 214px; text-align: center; }

  .person { position: absolute; left: 172px; top: 180px; }
  .person-name { color: var(--brand-red); font-weight: 700; font-size: 22px; line-height: 1.2; }
  .person-title { color: var(--accent-gold); font-weight: 600; font-size: 15px; line-height: 1.3; }

  .contact-list {
    position: absolute;
    right: 26px;
    top: 260px;
    list-style: none;
  }
  .contact-item {
    display: flex;
    align-items: center;
    justify-content: flex-end;
    gap: 12px;
    height: 23px;
    color: var(--text-white);
    font-size: 15px;
  }
  .contact-icon { width: 15px; height: 15px; fill: var(--accent-gold); }
</style>
</head>
<body>

<section class="card card-front" aria-label="Business card front">
  <svg class="swoosh" viewBox="0 0 614 352" preserveAspectRatio="none" aria-hidden="true">
    <path d="M10 352 C 250 326, 500 232, 612 0 L 614 0 L 614 352 Z" fill="var(--flame-orange)"/>
    <path d="M24 352 C 260 332, 520 240, 614 6 L 614 352 Z" fill="var(--brand-red)"/>
  </svg>

  <div class="brand-mark front-mark" aria-hidden="true"></div>
  <div class="wordmark front-wordmark">
    <span class="name">VALCORNE</span>
    <span class="tagline">HEALTH CARE MARKETING</span>
  </div>

  <div class="person">
    <p class="person-name">Marla Tenwick</p>
    <p class="person-title">CEO</p>
  </div>

  <ul class="contact-list">
    <li class="contact-item">(512)638-2974
      <svg class="contact-icon" viewBox="0 0 24 24" aria-hidden="true"><path d="M6.6 10.8a15.1 15.1 0 0 0 6.6 6.6l2.2-2.2a1 1 0 0 1 1-.25 11.4 11.4 0 0 0 3.6.57 1 1 0 0 1 1 1V20a1 1 0 0 1-1 1A17 17 0 0 1 3 4a1 1 0 0 1 1-1h3.5a1 1 0 0 1 1 1c0 1.25.2 2.45.57 3.57a1 1 0 0 1-.25 1z"/></svg>
    </li>
    <li class="contact-item">marla@valcorne.com
      <svg class="contact-icon" viewBox="0 0 24 24" aria-hidden="true"><path d="M2 5h20v14H2z M3.5 6.5 12 13l8.5-6.5" fill="var(--accent-gold)" stroke="var(--brand-red)" stroke-width="1.6"/></svg>
    </li>
    <li class="contact-item">www.valcorne.com
      <svg class="contact-icon" viewBox="0 0 24 24" aria-hidden="true"><circle cx="12" cy="12" r="11"/><path d="M8 6c2 1 1 3 3 4s0 3 2 4-1 4-1 6M15 4c-1 2 2 3 4 3" fill="none" stroke="var(--brand-red)" stroke-width="1.6"/></svg>
    </li>
  </ul>
</section>

<section class="card card-back" aria-label="Business card back">
  <div class="brand-mark back-mark" aria-hidden="true"></div>
  <div class="wordmark back-wordmark">
    <span class="name">VALCORNE</span>
    <span class="tagline">HEALTH CARE MARKETING</span>
  </div>
</section>

</body>
</html>
```